Letterhead for a German Distribution/Manufacturing Company

We need a professional Letterhead in a unique Design.
not to playful.
The Letterhead has to show show that we are a international company with headquater in Germany.
all details like adress, Vat Tax Number, Bank Accout, Eori, email, Company number has to be on the Letterhead.
for example use: VAT TAX DE5470318 Bank Account: Kestrel Bank IBAN DE412058731ß204683 Swift: MORV0417352 EORI 3150428697 Company Number: HRB 51806 Adress: VOLMINTA UG Ahornweg 7 Postal Code 06384 City Burgstädt Country: Germany Email: info@volminta-example.com
the design can be colored but doesnt have to be
Industry/Entity Type
Manufacturing and international distribution
Requirements
Must have
- show that we are a international company with headquater in Germany. our company infos and logo

```html
<!DOCTYPE html>
<html lang="en">
<head>
<meta charset="utf-8">
<title>VOLMINTA Letterhead</title>
<link href="https://fonts.googleapis.com/css2?family=Lato:wght@400&family=Open+Sans:wght@400&family=Roboto:wght@400&display=swap" rel="stylesheet">
<style>
  :root {
    --backdrop: #dedede;
    --paper: #f8f8f8;
    --ink-dark: #444444;
    --ink-body: #676767;
    --mark: #4a4a4a;
    --signature-tone: #e6e8ee;
  }
  * { margin: 0; padding: 0; box-sizing: border-box; }
  html, body {
    width: 1153px; height: 1200px; overflow: hidden;
    background: var(--backdrop);
  }
  .letterhead {
    position: absolute; left: 218px; top: 166px;
    width: 618px; height: 861px;
    background: var(--paper);
    box-shadow: 0 5px 18px rgba(0,0,0,0.12);
  }
  .brand {
    position: absolute; left: 62px; top: 53px;
    display: flex; align-items: center; gap: 8px;
  }
  .brand-dot {
    width: 34px; height: 34px; border-radius: 50%;
    background: var(--mark);
  }
  .brand-name {
    font-family: "Lato", sans-serif; font-weight: 400;
    font-size: 29px; letter-spacing: 0.3px; color: var(--mark);
    line-height: 1;
  }
  .company-info {
    position: absolute; right: 50px; top: 50px;
    display: flex; gap: 14px;
    font-family: "Roboto", sans-serif; font-size: 10.8px;
    line-height: 13.2px; color: var(--ink-dark);
  }
  .company-address { font-style: normal; white-space: nowrap; }
  .company-contact { white-space: nowrap; }
  .contact-line { display: flex; align-items: center; gap: 6px; }
  .contact-line svg { width: 9px; height: 9px; fill: var(--ink-dark); flex: none; }
  .letter-body {
    position: absolute; left: 62px; top: 213px; width: 494px;
    font-family: "Open Sans", sans-serif; font-size: 11.3px;
    line-height: 16.2px; color: var(--ink-body);
  }
  .letter-body p { margin-bottom: 16.2px; text-align: justify; }
  .letter-body .salutation, .letter-body .closing { text-align: left; }
  .signature {
    position: absolute; left: 62px; top: 641px;
    width: 70px; height: 65px;
    background: var(--signature-tone); border-radius: 3px;
  }
  .company-register {
    position: absolute; left: 0; right: 0; top: 795px;
    text-align: center;
    font-family: "Roboto", sans-serif; font-size: 10.6px;
    line-height: 16.2px; color: var(--ink-dark);
  }
  .sep { display: inline-block; width: 2px; height: 8px; background: var(--ink-dark); margin: 0 4px; vertical-align: -1px; }
</style>
</head>
<body>
<main class="letterhead">
  <header>
    <div class="brand">
      <span class="brand-dot"></span>
      <span class="brand-name">VOLMINTA</span>
    </div>
    <div class="company-info">
      <address class="company-address">
        VOLMINTA UG<br>
        Ahornweg 7 06384<br>
        City Talbrunn Germany
      </address>
      <div class="company-contact">
        <div class="contact-line">
          <svg viewBox="0 0 12 12"><path d="M1 4.5C1 2 3.5 1.5 6 1.5S11 2 11 4.5H8.5V3.6h-5v.9zM2.5 6l1.5-1.5h4L9.5 6v4.5h-7zM6 6.6a1.5 1.5 0 100 3 1.5 1.5 0 000-3z"/></svg>
          <span>729.555.0148</span>
        </div>
        <div class="contact-line">
          <svg viewBox="0 0 12 12"><path d="M1 2.5h10v1L6 6.5 1 3.5zM1 4.8l5 3 5-3v4.7H1z"/></svg>
          <span>info@volminta-example.com</span>
        </div>
        <div class="contact-line">
          <svg viewBox="0 0 12 12"><path d="M6 .8a5.2 5.2 0 100 10.4A5.2 5.2 0 006 .8zM3 3.2l2 .6.5 1.6-1.5 1 .4 2-1.6-1.2-.6-2.4zM7 2.2l1.8.8 1 1.8-1.6.5-1.4-1.2z"/></svg>
          <span>www.volminta-example.com</span>
        </div>
      </div>
    </div>
  </header>

  <section class="letter-body">
    <p class="salutation">Dear customer,</p>
    <p>Lorem ipsum dolor sit amet, consectetur adipisicing elit, sed do eiusmod tempor incididunt ut labore et dolore magna aliqua. Ut enim ad minim veniam, quis nostrud exercitation ullamco laboris nisi ut aliquip ex ea commodo consequat. Duis aute irure dolor in reprehenderit in voluptate velit esse cillum dolore eu fugiat nulla pariatur. Excepteur sint occaecat cupidatat non proident, sunt in culpa qui officia deserunt mollit anim id est laborum.</p>
    <p>Lorem ipsum dolor sit amet, consectetur adipisicing elit, sed do eiusmod tempor incididunt ut labore et dolore magna aliqua. Ut enim ad minim veniam, quis nostrud exercitation ullamco laboris nisi ut aliquip ex ea commodo consequat. Duis aute irure dolor in reprehenderit in voluptate velit esse cillum dolore eu fugiat nulla pariatur. Excepteur sint occaecat cupidatat non proident, sunt in culpa qui officia deserunt mollit anim id est laborum.</p>
    <p>Lorem ipsum dolor sit amet, consectetur adipisicing elit, sed do eiusmod tempor incididunt ut labore et dolore magna aliqua. Ut enim ad minim veniam, quis nostrud exercitation ullamco laboris nisi ut aliquip ex ea commodo consequat. Duis aute irure dolor in reprehenderit in voluptate velit esse cillum dolore eu fugiat nulla pariatur. Excepteur sint occaecat cupidatat non proident, sunt in culpa qui officia deserunt mollit anim id est laborum.</p>
    <p>Lorem ipsum dolor sit amet, consectetur adipisicing elit, sed do eiusmod tempor incididunt ut labore et dolore magna aliqua. Ut enim ad minim veniam, quis nostrud exercitation ullamco laboris nisi ut aliquip ex ea commodo consequat. Duis aute irure dolor in reprehenderit.</p>
    <p class="closing">Yours Sincerely,</p>
  </section>

  <div class="signature" role="img" aria-label="Handwritten signature of the sender"></div>

  <footer class="company-register">
    <div>VAT TAX DE5470318<span class="sep"></span>Bank Account: Kestrel Bank IBAN DE412058731ß204683</div>
    <div>Swift: MORV0417352 EORI 3150428697<span class="sep"></span>Company Number: HRB 51806</div>
  </footer>
</main>
</body>
</html>
```